Design for the A4 Letterhead, envelope and A4 Folder

Design have to be clean, professional, unique (eye catchy) and high end.
Colors: Yellow (Code: 803C), Darker Grey and Black or white (optional)
Logo can be in white or black

Letterhead:
Contain: 1. Korvane Logo
2. Slogan "MADE WITH PRIDE"
3. Company information:
Korvane Valves Pte. Ltd. (Singapore)
Registration no: 201947215K
Tel: (65) 6418 2904
Fax: (65) 6472 9186
Email: sales@korvanevalves.example
Website: http://www.korvanevalves.example
4. Logo watermark

Envelope:
Contain: 1. Korvane Logo
3. website: http://www.korvanevalves.example and email address:
sales@korvanevalves.example
4. Logo watermark

Folder:
Contain: 1. Korvane Logo
3. Company's information:
Tel: (65) 6418 2904
Fax: (65) 6472 9186
4. QR Code
5. Logo watermark
6. On the inside there is a space to insert business card. Contrast colors
between the inside and cover.
Updates

For the Folder design, please be informed that we would prefer to have the Korvane logo on the left hand side of the cover page, rather than on the right hand side.And also if we could highlight the "Made with Pride" slogan with either the yellow box or black/grey box depending on the background color.For the Envelope design,it does not matter where the position of the logo is. But please also highlight the "Made with Pride" Slogan For the Letterhead design, the position of the logo must be on the left hand side and the slogan must be highlighted. In addition, please include the following company information (only for the letterhead design)Korvane Valves Pte. Ltd. (Singapore)Registration no: 200308878MTel: (65) 6535 3735Fax: (65) 6533 3570Email: sales@dynatechpumps.comWebsite: http://www.korvanevalves.example Added Wednesday, August 2, 2017

Target Market(s)

Business to Business, High End market

Industry/Entity Type

It Professional

Font styles to use
Serif

Requirements
Must have
• Design have to be clean, professional, unique (eye catchy) and high end.
Nice to have
• color contrast but still maintaining the professionalism and the seriousness
Should not have
• Messy look, futuristic look, too crowded

```html
<!DOCTYPE html>
<html lang="en">
<head>
<meta charset="utf-8">
<title>Korvane Valves – Letterhead</title>
<link rel="stylesheet" href="https://fonts.googleapis.com/css2?family=Open+Sans:wght@400;700&family=Oswald:wght@300&display=swap">
<style>
  :root {
    --backdrop: #e4d77a;
    --paper: #ffffff;
    --brand-yellow: #fbe122;
    --brand-grey: #a7a9ac;
    --ink: #1a1a1a;
    --ink-soft: #555555;
    --watermark: #f1f1f1;
  }
  * { margin: 0; padding: 0; box-sizing: border-box; }
  html, body {
    width: 1200px; height: 784px; overflow: hidden;
    background: var(--backdrop);
  }
  .canvas {
    width: 1200px; height: 784px;
    display: flex; align-items: center; justify-content: center;
  }
  .letterhead {
    position: relative;
    width: 523px; height: 740px;
    background: var(--paper);
    box-shadow: 0 6px 18px rgba(0,0,0,0.12);
    overflow: hidden;
  }
  /* corner tabs */
  .edge-tab { position: absolute; width: 6px; }
  .edge-tab--left { left: 0; }
  .edge-tab--right { right: 0; }
  .edge-tab--yellow { top: 0; height: 16px; background: var(--brand-yellow); }
  .edge-tab--grey { top: 16px; height: 34px; background: var(--brand-grey); }

  /* bottom band */
  .bottom-band { position: absolute; bottom: 0; height: 7px; }
  .bottom-band--yellow { left: 0; width: 68%; background: var(--brand-yellow); }
  .bottom-band--grey { left: 68%; right: 0; background: var(--brand-grey); }

  /* brand */
  .brand {
    position: absolute; top: 20px; left: 24px;
    display: flex; align-items: center; gap: 8px;
  }
  .brand__dot {
    width: 22px; height: 22px; border-radius: 50%;
    background: var(--ink);
  }
  .brand__name {
    font-family: "Open Sans", sans-serif;
    font-weight: 700; font-size: 19px; letter-spacing: 0.5px;
    color: var(--ink); text-transform: uppercase;
  }

  /* contact block */
  .contact {
    position: absolute; top: 24px; right: 22px;
    font-family: "Open Sans", sans-serif;
    font-size: 7px; line-height: 10px; color: var(--ink-soft);
    list-style: none;
  }
  .contact__company { font-weight: 700; color: var(--ink); font-size: 7.5px; margin-bottom: 1px; }
  .contact__item { display: flex; align-items: center; gap: 4px; }
  .contact__item::before {
    content: ""; width: 5px; height: 5px; border-radius: 50%;
    background: var(--ink-soft);
  }

  /* watermark */
  .watermark {
    position: absolute; left: 190px; top: 555px;
    width: 150px; height: 150px; border-radius: 50%;
    background: var(--watermark);
  }

  /* slogan */
  .slogan {
    position: absolute; right: 20px; bottom: 14px;
    font-family: "Oswald", sans-serif; font-weight: 300;
    font-size: 17px; letter-spacing: 1px;
    color: var(--brand-yellow);
  }
</style>
</head>
<body>
<main class="canvas">
  <article class="letterhead">
    <span class="edge-tab edge-tab--left edge-tab--yellow"></span>
    <span class="edge-tab edge-tab--left edge-tab--grey"></span>
    <span class="edge-tab edge-tab--right edge-tab--yellow"></span>
    <span class="edge-tab edge-tab--right edge-tab--grey"></span>

    <header class="brand">
      <span class="brand__dot"></span>
      <span class="brand__name">Korvane</span>
    </header>

    <ul class="contact">
      <li class="contact__company">Korvane Valves Pte. Ltd. (Singapore)</li>
      <li class="contact__item">Regd. No. 201947215K</li>
      <li class="contact__item">(65) 6418 2904</li>
      <li class="contact__item">(65) 6472 9186</li>
      <li class="contact__item">sales@korvanevalves.example</li>
      <li class="contact__item">www.korvanevalves.example</li>
    </ul>

    <div class="watermark" aria-hidden="true"></div>

    <p class="slogan">MADE WITH PRIDE</p>

    <span class="bottom-band bottom-band--yellow"></span>
    <span class="bottom-band bottom-band--grey"></span>
  </article>
</main>
</body>
</html>
```